Need a redesign for our Wordpress Credit report website

Hi, We need someone to redesign our Wordpress credit report website, lumenledger.co.za. The designer will be responsible for the following pages:
- home page
- blog page
- single post
- dashboard
- credit report page

About LumenLedger.co.za
Lumen Ledger is a consumer focussed credit report platform where South African citizens can get an easy to understand credit report that shows them where to improve their credit scores.

```html
<!DOCTYPE html>
<html lang="en">
<head>
<meta charset="utf-8">
<title>Lumen Ledger – Check your credit score</title>
<link rel="stylesheet" href="https://fonts.googleapis.com/css2?family=Roboto:wght@400;500;700&display=swap">
<style>
:root{
  --blue:#1f4fbd;
  --blue-dark:#1a43a6;
  --blue-title:#1c4ab3;
  --green:#7cc12a;
  --green-dark:#6aad1f;
  --text:#555b66;
  --heading:#1e2430;
  --white:#ffffff;
  --star:#f5a623;
  --line:#e4e7ee;
}
*{box-sizing:border-box;margin:0;padding:0}
html,body{width:1200px;height:4373px;overflow:hidden}
body{font-family:'Roboto',Arial,sans-serif;color:var(--text);background:var(--white)}
.page{position:relative;width:1200px;height:4373px;overflow:hidden}
.abs{position:absolute}
.bg-svg{position:absolute;left:0;display:block}
.logo-name{position:absolute;font-size:30px;font-weight:400;color:var(--white);letter-spacing:.5px;text-transform:uppercase;white-space:nowrap}
/* nav */
.nav{position:absolute;top:44px;left:462px;display:flex;gap:31px}
.nav a{color:var(--white);font-size:14px;font-weight:500;text-decoration:none}
.btn{display:inline-flex;align-items:center;justify-content:center;gap:8px;background:var(--green);color:var(--white);font-weight:700;font-size:13px;text-transform:uppercase;text-decoration:none;border-radius:2px}
.btn-dot{width:12px;height:12px;border-radius:50%;background:var(--white)}
.login{position:absolute;left:967px;top:32px;width:119px;height:44px}
/* hero */
.hero-title{position:absolute;left:109px;top:228px;font-size:37px;line-height:43px;font-weight:400;color:var(--white);text-transform:uppercase}
.ticks{position:absolute;left:109px;top:333px;list-style:none}
.ticks li{display:flex;align-items:center;gap:20px;color:var(--white);font-size:15px;height:30.3px}
.tick{width:15px;height:15px;border-radius:50%;background:var(--green);display:flex;align-items:center;justify-content:center}
.form-card{position:absolute;left:701px;top:148px;width:338px;height:378px;background:var(--white);box-shadow:0 6px 24px rgba(0,0,0,.18)}
.form-head{height:59px;background:var(--blue-dark);color:var(--white);font-size:17px;font-weight:500;text-transform:uppercase;display:flex;align-items:center;justify-content:center}
.field{position:absolute;height:40px;border:1px solid var(--line);font-size:12px;color:#666;display:flex;align-items:center;padding-left:18px;box-shadow:0 1px 3px rgba(0,0,0,.06)}
.agree{position:absolute;left:33px;top:290px;display:flex;align-items:center;gap:14px;font-size:12px;color:#555}
.radio{width:15px;height:15px;border:1px solid #bbb;border-radius:50%}
.show-btn{position:absolute;left:30px;top:322px;width:279px;height:38px}
/* section heading */
.h2{position:absolute;font-size:31px;font-weight:700;text-transform:uppercase;color:var(--blue-title)}
.h2 .g{color:var(--green)}
.h2-white{color:var(--white)}
.rule{position:absolute;height:3px;width:40px;background:var(--green)}
.rule-white{background:var(--white)}
/* about */
.about-text{position:absolute;left:658px;top:874px;width:430px;font-size:15px;line-height:25px;text-align:justify}
.about-text p+p{margin-top:25px}
.learn{position:absolute;left:658px;top:1103px;width:150px;height:44px}
/* features */
.feature{position:absolute;display:flex;align-items:center;gap:17px;color:var(--white);font-size:14px;line-height:20px;width:260px}
.f-icon{flex:none;width:62px;height:62px;border-radius:50%;background:var(--green);display:flex;align-items:center;justify-content:center}
/* testimonials */
.t-card{position:absolute;top:2025px;width:475px;height:278px;background:var(--white);border-radius:10px;box-shadow:0 2px 10px rgba(0,0,0,.14)}
.t-photo{position:absolute;left:172px;top:-47px;width:130px;height:130px;border-radius:50%}
.t-quote{position:absolute;left:216px;top:74px;width:42px;height:28px;display:flex;gap:6px}
.t-quote span{flex:1;background:var(--green);border-radius:10px 10px 2px 10px}
.t-text{position:absolute;left:36px;top:120px;width:403px;text-align:center;font-size:14px;line-height:24px}
.stars{position:absolute;left:0;right:0;top:228px;text-align:center;color:var(--star);font-size:17px;letter-spacing:2px}
.reviews{position:absolute;left:490px;top:2350px;width:218px;height:44px}
/* why */
.why{position:absolute;width:288px;height:288px;border-radius:50%;background:var(--white);display:flex;flex-direction:column;align-items:center;text-align:center;padding:0 34px;box-shadow:0 0 0 7px var(--green)}
.why-icon{margin-top:52px;height:60px}
.why h3{margin-top:22px;font-size:16px;line-height:20px;font-weight:700;color:var(--heading)}
.why p{margin-top:16px;font-size:13px;line-height:21px}
/* posts */
.col-title{position:absolute;top:3276px;font-size:21px;font-weight:700;color:var(--blue-title);text-transform:uppercase}
.ph{position:absolute;border-radius:2px}
.post-title{position:absolute;font-size:16px;line-height:22px;font-weight:700;color:var(--heading);width:170px}
.view-all{position:absolute;top:3745px;font-size:12px;font-weight:700;color:var(--green);text-decoration:underline;display:flex;align-items:center;gap:8px}
.view-all i{width:11px;height:11px;border-radius:50%;background:var(--green);display:inline-block}
/* footer */
.f-col{position:absolute;top:4012px;color:var(--white)}
.f-col h4{font-size:17px;font-weight:700;margin-bottom:17px}
.f-col li{list-style:none;font-size:13px;height:31px;display:flex;gap:14px}
.f-col li b{font-weight:700}
.contact li{height:auto;margin-bottom:18px;line-height:20px;width:230px}
.f-rule{position:absolute;left:112px;top:4268px;width:976px;height:1px;background:rgba(255,255,255,.5)}
.copy{position:absolute;left:0;right:0;top:4311px;text-align:center;color:var(--white);font-size:14px}
</style>
</head>
<body>
<div class="page">

<!-- HERO -->
<svg class="bg-svg" style="top:0" width="1200" height="720" viewBox="0 0 1200 720" aria-hidden="true">
  <defs><linearGradient id="heroG" x1="0" y1="0" x2="1" y2="1"><stop offset="0" stop-color="#2357c4"/><stop offset="1" stop-color="#1b46ab"/></linearGradient></defs>
  <path d="M0 0H1200V300Q820 560 0 650Z" fill="url(#heroG)"/>
  <path d="M0 650Q820 560 1200 300V355Q820 640 0 708Z" fill="#7cc12a"/>
</svg>
<div class="logo-name" style="left:135px;top:36px">Lumen Ledger</div>
<nav class="nav"><a>Home</a><a>Articles</a><a>About</a><a>Credit Report</a><a>Blog</a><a>Contact</a></nav>
<a class="btn login">Log in <span class="btn-dot" style="border-radius:2px;width:9px;height:10px"></span></a>
<h1 class="hero-title">Check your credit<br>score within seconds</h1>
<ul class="ticks">
  <li><span class="tick"><svg width="9" height="9" viewBox="0 0 10 10"><path d="M1 5l3 3 5-6" stroke="#fff" stroke-width="2" fill="none"/></svg></span>See your most recent credit score</li>
  <li><span class="tick"><svg width="9" height="9" viewBox="0 0 10 10"><path d="M1 5l3 3 5-6" stroke="#fff" stroke-width="2" fill="none"/></svg></span>Get access to your full credit profile</li>
  <li><span class="tick"><svg width="9" height="9" viewBox="0 0 10 10"><path d="M1 5l3 3 5-6" stroke="#fff" stroke-width="2" fill="none"/></svg></span>See who has been looking at your profile</li>
  <li><span class="tick"><svg width="9" height="9" viewBox="0 0 10 10"><path d="M1 5l3 3 5-6" stroke="#fff" stroke-width="2" fill="none"/></svg></span>See if you have any adverse or Blacklistings</li>
</ul>
<form class="form-card">
  <div class="form-head">Get started now</div>
  <div class="field" style="left:30px;top:80px;width:279px">ID Num</div>
  <div class="field" style="left:30px;top:131px;width:137px">First Name</div>
  <div class="field" style="left:172px;top:131px;width:137px">Last Name</div>
  <div class="field" style="left:30px;top:182px;width:279px">Primary Email</div>
  <div class="field" style="left:30px;top:233px;width:279px">Mobile Number</div>
  <div class="agree"><span class="radio"></span>I agree with the terms and conditions</div>
  <a class="btn show-btn">Show my score</a>
</form>

<!-- ABOUT -->
<div class="abs" role="img" aria-label="Credit report dashboard shown on a desktop monitor and tablet in front of a soft blue blob" style="left:175px;top:733px;width:345px;height:440px;border-radius:48% 52% 20% 20%;background:linear-gradient(160deg,#8fb1e3,#e9eef7 70%)"></div>
<h2 class="h2" style="left:658px;top:792px">About <span class="g">us</span></h2>
<div class="rule" style="left:658px;top:840px"></div>
<div class="about-text">
  <p>lumenledger.co.za (LL) is a web based platform that enables credit active consumers to get direct access to their credit scores and profiles in an easy to understand and interactive online report.</p>
  <p>LL launched in November 2013 and has since helped thousands of South Africans get access to their credit reports, many people becoming regular users on our platform</p>
</div>
<a class="btn learn">Learn more <span class="btn-dot"></span></a>

<!-- FEATURES -->
<svg class="bg-svg" style="top:1278px" width="1200" height="533" viewBox="0 0 1200 533" aria-hidden="true">
  <rect width="1200" height="533" fill="#1f4fbd"/>
  <circle cx="915" cy="533" r="165" fill="#7cc12a"/>
</svg>
<h2 class="h2 h2-white" style="left:110px;top:1337px">System features</h2>
<div class="rule rule-white" style="left:110px;top:1390px"></div>
<div class="feature" style="left:110px;top:1423px"><span class="f-icon"><svg width="30" height="30" viewBox="0 0 30 30"><circle cx="9" cy="9" r="4" fill="#fff"/><circle cx="21" cy="9" r="4" fill="#fff"/><path d="M3 26c0-6 12-6 12 0M15 26c0-6 12-6 12 0" fill="#fff"/></svg></span>Dispute generator - easily manage disputes</div>
<div class="feature" style="left:378px;top:1423px"><span class="f-icon"><svg width="30" height="30" viewBox="0 0 30 30"><circle cx="15" cy="15" r="11" fill="none" stroke="#fff" stroke-width="3"/><text x="15" y="20" fill="#fff" font-size="13" font-weight="700" text-anchor="middle" font-family="Roboto,sans-serif">$</text></svg></span>Budget tool - easily create a budget</div>
<div class="feature" style="left:110px;top:1508px"><span class="f-icon"><svg width="30" height="30" viewBox="0 0 30 30"><rect x="5" y="6" width="20" height="18" rx="2" fill="#fff"/><path d="M9 11h12M9 15h12M9 19h8" stroke="#7cc12a" stroke-width="2"/></svg></span>Improve your credit score eBook</div>
<div class="feature" style="left:378px;top:1508px"><span class="f-icon"><svg width="30" height="30" viewBox="0 0 30 30"><rect x="6" y="4" width="18" height="22" rx="2" fill="#fff"/><path d="M10 10h10M10 14h10M10 18h10M10 22h6" stroke="#7cc12a" stroke-width="2"/></svg></span>Personal Budgeting Spreadsheet</div>
<div class="feature" style="left:110px;top:1593px"><span class="f-icon"><svg width="30" height="30" viewBox="0 0 30 30"><rect x="5" y="5" width="20" height="20" fill="#fff"/><path d="M9 5v20M21 5v20" stroke="#7cc12a" stroke-width="2"/><path d="M13 11l5 4-5 4z" fill="#7cc12a"/></svg></span>Perfect score video course</div>
<div class="feature" style="left:378px;top:1593px"><span class="f-icon"><svg width="30" height="30" viewBox="0 0 30 30"><ellipse cx="12" cy="20" rx="7" ry="3" fill="#fff"/><ellipse cx="12" cy="15" rx="7" ry="3" fill="#fff"/><circle cx="21" cy="10" r="6" fill="#fff"/></svg></span>Personal Finance Video Tutorials</div>
<div class="feature" style="left:110px;top:1683px"><span class="f-icon"><svg width="30" height="30" viewBox="0 0 30 30"><path d="M5 17a10 10 0 0120 0" fill="none" stroke="#fff" stroke-width="3"/><rect x="3" y="16" width="5" height="8" rx="2" fill="#fff"/><rect x="22" y="16" width="5" height="8" rx="2" fill="#fff"/><text x="15" y="25" fill="#fff" font-size="9" font-weight="700" text-anchor="middle" font-family="Roboto,sans-serif">24</text></svg></span>Dedicated 24/7 Support</div>
<div class="abs" role="img" aria-label="Two hands holding a tablet showing the credit report dashboard" style="left:636px;top:1383px;width:564px;height:300px;border-radius:14px;background:linear-gradient(135deg,#1a1f33,#3a3f58)"></div>

<!-- TESTIMONIALS -->
<svg class="bg-svg" style="top:1811px" width="1200" height="684" viewBox="0 0 1200 684" aria-hidden="true">
  <circle cx="-60" cy="200" r="135" fill="#7cc12a"/>
  <circle cx="1100" cy="710" r="130" fill="#7cc12a"/>
</svg>
<h2 class="h2" style="left:0;right:0;top:1895px;text-align:center">User <span class="g">testimonials</span></h2>
<div class="rule" style="left:580px;top:1950px"></div>
<div class="t-card" style="left:110px">
  <div class="t-photo" role="img" aria-label="Photo of a smiling family" style="background:linear-gradient(135deg,#c9d6ea,#8a9cbc)"></div>
  <div class="t-quote"><span></span><span></span></div>
  <p class="t-text">The report was accurate and gave me a good understanding of my current credit status. I found it interesting the way the scoring worked and really enjoyed reading it...guess because I am doing well with managing credit.</p>
  <div class="stars">★★★★★</div>
</div>
<div class="t-card" style="left:613px">
  <div class="t-photo" role="img" aria-label="Black and white photo of a smiling couple" style="background:linear-gradient(135deg,#d8d8d8,#6f6f6f)"></div>
  <div class="t-quote"><span></span><span></span></div>
  <p class="t-text">The report was accurate and gave me a good understanding of my current credit status. I found it interesting the way the scoring worked and really enjoyed reading it...guess because I am doing well with managing credit.</p>
  <div class="stars">★★★★★</div>
</div>
<a class="btn reviews">View Rateway reviews <span class="btn-dot"></span></a>

<!-- WHY -->
<svg class="bg-svg" style="top:2495px" width="1200" height="607" viewBox="0 0 1200 607" aria-hidden="true">
  <rect width="1200" height="607" fill="#1f4fbd"/>
  <circle cx="40" cy="700" r="170" fill="#7cc12a"/>
  <circle cx="640" cy="320" r="200" fill="none" stroke="#7cc12a" stroke-width="8"/>
  <circle cx="270" cy="345" r="168" fill="none" stroke="#7cc12a" stroke-width="6" stroke-dasharray="300 760"/>
</svg>
<h2 class="h2 h2-white" style="left:0;right:0;top:2552px;text-align:center">Why get your score from us?</h2>
<div class="rule rule-white" style="left:580px;top:2607px"></div>
<div class="why" style="left:114px;top:2690px">
  <svg class="why-icon" width="74" height="60" viewBox="0 0 74 60"><rect x="2" y="4" width="70" height="52" rx="4" fill="#7cc12a"/><circle cx="22" cy="24" r="8" fill="#fff"/><path d="M10 46c0-10 24-10 24 0z" fill="#fff"/><path d="M42 22h22M42 32h22M42 42h16" stroke="#fff" stroke-width="4"/></svg>
  <h3>We don't abuse your personal information</h3>
  <p>Companies that give out free credit scores use your information to sell you financial products.</p>
</div>
<div class="why" style="left:462px;top:2690px;box-shadow:0 0 0 14px var(--green)">
  <svg class="why-icon" width="60" height="66" viewBox="0 0 60 66"><rect x="6" y="2" width="40" height="52" fill="#7cc12a"/><rect x="14" y="10" width="40" height="54" fill="#7cc12a" stroke="#fff" stroke-width="2"/><path d="M22 22h24M22 30h24M22 38h24M22 46h16" stroke="#fff" stroke-width="3"/></svg>
  <h3>Our report is super easy to understand</h3>
  <p>Companies that give out free credit scores use your information to sell you financial products.</p>
</div>
<div class="why" style="left:806px;top:2690px">
  <svg class="why-icon" width="74" height="60" viewBox="0 0 74 60"><circle cx="37" cy="12" r="11" fill="#7cc12a"/><path d="M31 12l4 4 8-8" stroke="#fff" stroke-width="3" fill="none"/><path d="M2 34l14-8 12 6 9-4 9 4 12-6 14 8-12 16-14-10-9 6-9-6-14 10z" fill="#7cc12a"/></svg>
  <h3>300,000 + South Africans have trusted us</h3>
  <p>Companies that give out free credit scores use your information to sell you financial products.</p>
</div>

<!-- RECENT POSTS -->
<svg class="bg-svg" style="top:3102px" width="1200" height="733" viewBox="0 0 1200 733" aria-hidden="true">
  <circle cx="1235" cy="380" r="125" fill="#7cc12a"/>
</svg>
<h2 class="h2" style="left:0;right:0;top:3178px;text-align:center">Recent <span class="g">posts</span></h2>
<h3 class="col-title" style="left:110px">Podcasts</h3>
<h3 class="col-title" style="left:444px">Recent post</h3>
<h3 class="col-title" style="left:783px">Categories</h3>

<div class="ph" role="img" aria-label="Couple looking at a phone and a bank card together" style="left:110px;top:3313px;width:318px;height:263px;background:linear-gradient(135deg,#6b4a33,#d89a3c 60%,#3c2a20)"></div>
<div class="abs" style="left:139px;top:3600px;font-size:17px;font-weight:700;color:var(--heading)">The Benefits Of Legal Cover</div>
<p class="abs" style="left:139px;top:3638px;width:275px;font-size:13px;line-height:22px">Have you ever been in a situation where you wished you had a lawyer on ...</p>
<div class="abs" style="left:139px;top:3697px;font-size:12px;font-weight:700;color:var(--blue-title);display:flex;gap:8px;align-items:center">READ MORE <i style="width:11px;height:11px;border-radius:50%;background:var(--blue-title);display:inline-block"></i></div>
<a class="view-all" style="left:139px">VIEW ALL <i></i></a>

<div class="ph" role="img" aria-label="Woman in yellow smiling at her phone" style="left:445px;top:3314px;width:137px;height:119px;background:linear-gradient(135deg,#e9e2d6,#e3b32b)"></div>
<div class="post-title" style="left:600px;top:3352px">Credit Report Q&amp;A Session 3</div>
<div class="ph" role="img" aria-label="Man working at a laptop" style="left:445px;top:3453px;width:137px;height:119px;background:linear-gradient(135deg,#cfcfcf,#4e4e4e)"></div>
<div class="post-title" style="left:600px;top:3490px">The Benefits of Legal Cover</div>
<div class="ph" role="img" aria-label="Man reviewing documents at a desk" style="left:445px;top:3589px;width:137px;height:119px;background:linear-gradient(135deg,#e7e3dc,#8e8579)"></div>
<div class="post-title" style="left:600px;top:3627px">Credit Life Insurance in South Africa</div>
<a class="view-all" style="left:473px">VIEW ALL <i></i></a>

<div class="ph" role="img" aria-label="Hands going over a credit report on a desk" style="left:784px;top:3314px;width:137px;height:119px;background:linear-gradient(135deg,#dfe6ee,#8296ad)"></div>
<div class="post-title" style="left:940px;top:3362px">Credit Report Tips</div>
<div class="ph" role="img" aria-label="Calculator and bank notes" style="left:784px;top:3453px;width:137px;height:119px;background:linear-gradient(135deg,#e4dfd8,#5d6c77)"></div>
<div class="post-title" style="left:940px;top:3501px">Finance Calculators</div>
<div class="ph" role="img" aria-label="Person counting bank notes" style="left:784px;top:3589px;width:137px;height:119px;background:linear-gradient(135deg,#ddd6cc,#7e7466)"></div>
<div class="post-title" style="left:940px;top:3627px">Personal Finance Tips</div>
<a class="view-all" style="left:813px">VIEW ALL <i></i></a>

<!-- FOOTER -->
<svg class="bg-svg" style="top:3830px" width="1200" height="543" viewBox="0 0 1200 543" aria-hidden="true">
  <rect width="1200" height="543" fill="#1f4fbd"/>
  <path d="M0 0H1200V5Q700 40 0 240Z" fill="#ffffff"/>
  <path d="M0 240Q700 40 1200 5V40Q700 90 0 278Z" fill="#7cc12a"/>
  <circle cx="30" cy="105" r="95" fill="#1f4fbd"/>
</svg>
<div class="logo-name" style="left:140px;top:4110px;font-size:30px">Lumen Ledger</div>
<div class="f-col" style="left:423px">
  <h4>Quick Links</h4>
  <ul><li><b>»</b>Home</li><li><b>»</b>About Us</li><li><b>»</b>Articles</li><li><b>»</b>Contact Us</li><li><b>»</b>Login</li></ul>
</div>
<div class="f-col" style="left:613px">
  <h4>Other Links</h4>
  <ul><li><b>»</b>General Terms Of Use</li><li><b>»</b>Exclusion Of Liability</li><li><b>»</b>Security Policy</li><li><b>»</b>Privacy Policy</li><li><b>»</b>Refund Policy</li></ul>
</div>
<div class="f-col contact" style="left:848px">
  <h4>Contact Us</h4>
  <ul>
    <li><svg width="12" height="16" viewBox="0 0 12 16" style="flex:none;margin-top:2px"><path d="M6 0a6 6 0 00-6 6c0 4 6 10 6 10s6-6 6-10a6 6 0 00-6-6z" fill="#fff"/><circle cx="6" cy="6" r="2.2" fill="#1f4fbd"/></svg>Sed ut perspiciatis unde omnis iste United States</li>
    <li><svg width="13" height="13" viewBox="0 0 13 13" style="flex:none;margin-top:3px"><path d="M3 0l2 3-1.5 2a8 8 0 004.5 4.5L10 8l3 2-1 3C6 13 0 7 0 1z" fill="#fff"/></svg>Tel No : +1 888 888 8888</li>
    <li><svg width="14" height="11" viewBox="0 0 14 11" style="flex:none;margin-top:4px"><rect width="14" height="11" rx="1" fill="#fff"/><path d="M0 1l7 5 7-5" stroke="#1f4fbd" fill="none"/></svg>Email : info@lumenledger.com</li>
  </ul>
</div>
<div class="f-rule"></div>
<p class="copy">© 2022 Lumen Ledger. All Rights Reserved</p>

</div>
</body>
</html>
```